Business card design for sustainable building and development company

Need a business card design for a new sustainable building and real estate development company in the San Francisco Bay area. Name of company is "Tovrin Advisors, LLC" and we provide "Sustainable building, energy and development services" for residential and non residential projects. We'd like the following colors used but not all area required: green, gray, blue. Design should communicate innovation, professionalism and sustainability. Our current website is www.tovrin-advisors.example. Another possible design idea is to have the following listed on the back of the card:
Certified: VERN QS, Eco Marker Rater, DOLM Rater, Terravue Inspector, KSO TQ Building Analyst. Its not a must but could be text that could be used for back of card. Overall, we are open to a simple, clean design and or one with more text than usual for a card.

Industry/Entity Type

Real Estate

Contact Information for Business Card

Name on card: Mark J. Halvik
Title for Name: Principal + Founder
Phone: 555.814.0627
Email: mhalvik@tovrin-advisors.example
Website: www.tovrin-advisors.example

Also, please add the following for address:
San Francisco, California

Requirements
Nice to have
• If you can integrate the outline of a skyline on the backside of the card and if it looks good, I would like to see the design
Should not have
• a barcode;

```html
<!DOCTYPE html>
<html lang="en">
<head>
<meta charset="utf-8">
<title>Tovrin Advisors – Business Card</title>
<link href="https://fonts.googleapis.com/css2?family=Montserrat:wght@400;600;700&display=swap" rel="stylesheet">
<style>
  :root {
    --green: #5cb947;
    --black: #1c1c1c;
    --paper-light: #ffffff;
    --paper-mid: #e4e4e4;
    --ink: #2a2a2a;
    --stage: #ecebe7;
  }
  html, body {
    margin: 0;
    width: 1057px;
    height: 1200px;
    overflow: hidden;
    background: var(--stage);
    font-family: "Montserrat", sans-serif;
  }
  .card {
    position: absolute;
    left: 108px;
    width: 840px;
    height: 480px;
    background: radial-gradient(ellipse at 60% 35%, var(--paper-light) 0%, var(--paper-mid) 100%);
    box-shadow: 0 10px 30px rgba(0,0,0,.18);
    overflow: hidden;
  }
  .card svg { position: absolute; inset: 0; }
  .card-front { top: 80px; }
  .card-back { top: 640px; }

  .brand {
    position: absolute;
    left: 48px;
    top: 52px;
    display: flex;
    align-items: center;
    gap: 14px;
  }
  .brand-dot {
    width: 52px; height: 52px;
    border-radius: 50%;
    background: var(--green);
  }
  .brand-name {
    color: var(--green);
    font-weight: 700;
    font-size: 34px;
    line-height: 1;
  }
  .brand-tagline {
    color: var(--green);
    font-size: 10.5px;
    font-weight: 600;
    letter-spacing: .3px;
    margin-top: 5px;
  }
  .person {
    position: absolute;
    left: 48px;
    top: 200px;
    color: var(--ink);
  }
  .person-name {
    font-size: 34px;
    font-weight: 400;
    letter-spacing: 3px;
    text-transform: uppercase;
  }
  .person-title {
    font-size: 16px;
    letter-spacing: 5px;
    text-transform: uppercase;
    margin-top: 4px;
  }
  .contact {
    position: absolute;
    display: flex;
    align-items: center;
    gap: 10px;
    color: #fff;
    font-size: 13px;
    font-weight: 600;
  }
  .icon {
    width: 22px; height: 22px;
    background: #fff;
    display: flex; align-items: center; justify-content: center;
  }
  .contact-address { left: 490px; top: 288px; }
  .contact-phone { left: 490px; top: 330px; }
  .contact-email { left: 48px; top: 443px; }
  .contact-web { left: 440px; top: 443px; }
</style>
</head>
<body>

<section class="card card-front" aria-label="Card front">
  <svg width="840" height="480" viewBox="0 0 840 480">
    <rect x="8" y="8" width="824" height="464" fill="none" stroke="var(--green)" stroke-width="16"/>
    <rect x="26" y="26" width="788" height="428" fill="none" stroke="var(--black)" stroke-width="10"/>
    <clipPath id="inner-frame"><rect x="31" y="31" width="778" height="418"/></clipPath>
    <g clip-path="url(#inner-frame)">
      <circle cx="200" cy="470" r="200" fill="none" stroke="var(--green)" stroke-width="26"/>
      <circle cx="200" cy="470" r="150" fill="var(--green)"/>
    </g>
  </svg>
</section>

<section class="card card-back" aria-label="Card back">
  <svg width="840" height="480" viewBox="0 0 840 480">
    <polygon class="band-green" points="0,360 400,360 470,250 840,250 840,430 0,430" fill="var(--green)"/>
    <rect class="band-black" x="470" y="275" width="370" height="90" fill="var(--black)"/>
    <rect class="band-black-base" x="0" y="430" width="840" height="50" fill="var(--black)"/>
  </svg>

  <div class="brand">
    <div class="brand-dot"></div>
    <div>
      <div class="brand-name">Tovrin Advisors</div>
      <div class="brand-tagline">Sustainable building, energy and development services</div>
    </div>
  </div>

  <div class="person">
    <div class="person-name">Mark J. Halvik</div>
    <div class="person-title">Principal + Founder</div>
  </div>

  <div class="contact contact-address">
    <span class="icon"><svg width="12" height="14" viewBox="0 0 12 14"><path d="M6 0a5 5 0 0 1 5 5c0 4-5 9-5 9S1 9 1 5a5 5 0 0 1 5-5z" fill="var(--black)"/><circle cx="6" cy="5" r="2" fill="#fff"/></svg></span>
    San Francisco, California
  </div>
  <div class="contact contact-phone">
    <span class="icon"><svg width="12" height="12" viewBox="0 0 12 12"><path d="M2 0h3l1 3-2 1.5a7 7 0 0 0 3.5 3.5L9 6l3 1v3a2 2 0 0 1-2 2A10 10 0 0 1 0 2a2 2 0 0 1 2-2z" fill="var(--black)"/></svg></span>
    555.814.0627
  </div>
  <div class="contact contact-email">
    <span class="icon"><svg width="14" height="10" viewBox="0 0 14 10"><rect width="14" height="10" fill="var(--black)"/><path d="M0 0l7 6 7-6" fill="none" stroke="#fff" stroke-width="1.2"/></svg></span>
    mhalvik@tovrin-advisors.example
  </div>
  <div class="contact contact-web">
    <span class="icon"><svg width="12" height="12" viewBox="0 0 12 12"><circle cx="6" cy="6" r="5" fill="none" stroke="var(--black)" stroke-width="1.4"/><path d="M1 6h10M6 1c-3 3-3 7 0 10M6 1c3 3 3 7 0 10" fill="none" stroke="var(--black)" stroke-width="1"/></svg></span>
    www.tovrin-advisors.example
  </div>
</section>

</body>
</html>
```